Looking for a dynamic business card for a pizzeria.

A business card with our food, logo, and space for name, title, email, website, phone. The card should convey quality, unique, amazing. On the front, I envision food photo or photos with the owners names and contact information. On the back, more food with locations, website, facebook, twitter, instagram icons. It should look polished, not cartoonish, or plain.
Target Market(s)
upscale, local food buyers, 30-50 years in age.
Industry/Entity Type
Restaurant
Contact Information for Business Card
Business Name: Bru'nettix, LLC
Website: www.brunettix.com
Back:
2 locations: (can list on the back of card)
1. Marlow Bay
4087 Corlan Avenue
Harlowe, WA 98314
360-481-5067
2. Linden Rise
7315 Wendmere Road
Harlowe, WA 98317
360-293-8840
front:
EDITABLE space for
Business name
Person's Name
title
2nd title
Email address
cell-phone number
Requirements
Must have
- logo
- my food photo or photos (no watermarks showing)
- locations on back
- Person contact information on front
- full bleed

```html
<!DOCTYPE html>
<html lang="en">
<head>
<meta charset="utf-8">
<title>Bru'nettix business card</title>
<link rel="stylesheet" href="https://fonts.googleapis.com/css2?family=Voltaire&family=Didact+Gothic&display=swap">
<style>
  :root {
    --backdrop: #e9e5de;
    --card-white: #ffffff;
    --brand-green: #2f6b3a;
    --brand-red: #c0181b;
    --ink: #3a3a3a;
    --ink-soft: #555555;
    --crust: #e8d2b0;
    --cheese: #f3e6cc;
    --topping: #d9826b;
  }
  * { box-sizing: border-box; margin: 0; padding: 0; }
  html, body { width: 1200px; height: 843px; overflow: hidden; }
  body {
    background: var(--backdrop);
    font-family: "Didact Gothic", sans-serif;
    color: var(--ink);
    position: relative;
  }
  .card {
    position: absolute;
    width: 540px;
    height: 309px;
    background: var(--card-white);
    overflow: hidden;
    box-shadow: 0 6px 18px rgba(0,0,0,0.18);
  }
  /* ---- back side: locations ---- */
  .card-back { left: 40px; top: 267px; }
  .food-photo {
    position: absolute;
    right: 0; top: 0;
    width: 380px; height: 215px;
    background: linear-gradient(160deg, var(--crust), var(--cheese) 45%, var(--topping) 80%, #d9b48d);
    -webkit-mask-image: linear-gradient(to right, transparent 0%, #000 45%);
    mask-image: linear-gradient(to right, transparent 0%, #000 45%);
  }
  .locations {
    position: absolute;
    left: 28px; top: 50px;
    font-size: 15px;
    line-height: 1.12;
    color: var(--ink-soft);
  }
  .location + .location { margin-top: 16px; }
  .location-name, .location-phone-label { color: var(--brand-green); }
  .brand-name {
    font-family: "Voltaire", sans-serif;
    color: var(--brand-green);
    letter-spacing: 1px;
    line-height: 1;
  }
  .card-back .brand-name {
    position: absolute;
    left: 28px; bottom: 28px;
    font-size: 40px;
  }
  /* ---- front side: person ---- */
  .card-front { left: 630px; top: 267px; }
  .card-front .shape { position: absolute; inset: 0; }
  .card-front .brand-name {
    position: absolute;
    left: 30px; top: 28px;
    font-size: 46px;
  }
  .person {
    position: absolute;
    left: 38px; top: 92px;
  }
  .person-name {
    font-size: 22px;
    color: var(--brand-green);
    letter-spacing: 0.5px;
  }
  .person-title { font-size: 15px; color: var(--brand-red); }
  .contact-list {
    position: absolute;
    left: 38px; top: 160px;
    list-style: none;
    font-size: 15px;
    color: var(--ink);
  }
  .contact-list li { display: flex; align-items: center; gap: 9px; height: 22px; }
  .contact-list svg { width: 14px; height: 14px; flex: none; }
  .social-spots {
    position: absolute;
    right: 22px; bottom: 22px;
    display: flex; gap: 10px;
  }
  .social-spots span {
    width: 18px; height: 18px;
    border-radius: 50%;
    background: var(--card-white);
    opacity: 0.9;
  }
</style>
</head>
<body>

<section class="card card-back" aria-label="Card back with locations">
  <div class="food-photo" role="img" aria-label="Photo of a pizza being topped with pepperoni"></div>
  <div class="locations">
    <div class="location">
      <div class="location-name">Linden Rise</div>
      <div>7315 Wendmere Road</div>
      <div>Harlowe, WA 98317</div>
      <div><span class="location-phone-label">Phone:</span>360-293-8840</div>
    </div>
    <div class="location">
      <div class="location-name">Marlow Bay</div>
      <div>4087 Corlan Avenue</div>
      <div>Harlowe, WA 98314</div>
      <div><span class="location-phone-label">Phone:</span>360-481-5067</div>
    </div>
  </div>
  <div class="brand-name">BRU'NETTIX</div>
</section>

<section class="card card-front" aria-label="Card front with contact details">
  <svg class="shape" viewBox="0 0 540 309" preserveAspectRatio="none" aria-hidden="true">
    <rect width="540" height="309" fill="var(--brand-red)"/>
    <path d="M0 0 H410 C490 70 505 170 440 232 C380 288 200 270 0 228 Z" fill="var(--card-white)"/>
  </svg>
  <div class="brand-name">BRU'NETTIX</div>
  <div class="person">
    <div class="person-name">DANIEL REYES</div>
    <div class="person-title">Founder</div>
  </div>
  <ul class="contact-list">
    <li>
      <svg viewBox="0 0 14 14" aria-hidden="true"><rect x="3.5" y="1" width="7" height="12" rx="1.2" fill="none" stroke="var(--brand-green)" stroke-width="1.5"/><circle cx="7" cy="11" r="0.8" fill="var(--brand-green)"/></svg>
      <span>689 512 7046</span>
    </li>
    <li>
      <svg viewBox="0 0 14 14" aria-hidden="true"><rect x="1" y="3" width="12" height="8.5" fill="var(--brand-green)"/><path d="M1.5 3.5 L7 8 L12.5 3.5" fill="none" stroke="#fff" stroke-width="1.2"/></svg>
      <span>name@brunettix.com</span>
    </li>
    <li>
      <svg viewBox="0 0 14 14" aria-hidden="true"><circle cx="7" cy="7" r="6" fill="var(--brand-green)"/><path d="M1 7 H13 M7 1 C4 4 4 10 7 13 M7 1 C10 4 10 10 7 13" fill="none" stroke="#fff" stroke-width="0.9"/></svg>
      <span>www.brunettix.com</span>
    </li>
  </ul>
  <div class="social-spots" aria-hidden="true"><span></span><span></span><span></span></div>
</section>

</body>
</html>
```